Dental office stationary (letterhead, envelopes), business cards, presentation folders

Nothing too dental outside of the logo. I will need all stationary, presentation folders, business cards. Would prefer to stay in the colors of the logo

Gordon Patel, DDS
Bright Haven Dental Implant Center
555-318-2790
info@brighthavendental.example
4817 NW Maple Crest Rd Unit B
Stuart, FL 00000

Also need appointment date and time
And cancellation policy
I want it to say “kindly ask for
A 48hr cancellation policy to avoid incurring a cancellation fee”

Industry/Entity Type

Dental

Colors
0054AA
0677BA
7BADD7
CADEEF
E8F1F8

Requirements
Must have
• Name of your office, name of doctor, address, phone number
Should not have
• Too much tooth/dental. Only the tooth in logo

```html
<!DOCTYPE html>
<html lang="en">
<head>
<meta charset="utf-8">
<title>Bright Haven Dental Implant Center – Stationery</title>
<link href="https://fonts.googleapis.com/css2?family=Arimo:wght@400&family=Roboto:wght@400;500;700&display=swap" rel="stylesheet">
<style>
  :root {
    --backdrop: #9a999a;
    --paper: #ffffff;
    --ink: #444444;
    --ink-soft: #555555;
    --teal: #15b39b;
    --cyan: #1ac2ee;
    --blue: #0a6cbb;
    --name-blue: #19a7da;
    --shadow: 0 2px 6px rgba(0,0,0,.35);
  }
  * { box-sizing: border-box; margin: 0; padding: 0; }
  html, body { width: 1200px; height: 807px; overflow: hidden; }
  body {
    background: var(--backdrop);
    font-family: "Roboto", sans-serif;
    color: var(--ink);
    position: relative;
  }
  .sheet { position: absolute; background: var(--paper); box-shadow: var(--shadow); overflow: hidden; }
  .footer-band {
    position: absolute; left: 0; bottom: 0; width: 100%;
    background: linear-gradient(90deg, var(--teal), var(--cyan) 45%, var(--blue));
  }

  .brand { position: absolute; font-family: "Roboto", sans-serif; font-weight: 400; color: var(--teal); text-align: center; white-space: nowrap; line-height: 1; }
  .brand__name { display: block; letter-spacing: .04em; }
  .brand__tag { display: block; letter-spacing: .32em; margin-top: .25em; }
  .brand--light { color: #ffffff; }

  .contact { position: absolute; font-size: 8.2px; line-height: 9.8px; color: var(--ink); white-space: nowrap; }
  .contact p { display: flex; align-items: center; gap: 2px; }
  .contact .gap { margin-top: 5.5px; }
  .contact .web { color: var(--teal); }
  .icon { width: 6px; height: 6px; flex: none; fill: var(--teal); }

  /* Letterhead */
  .letterhead { left: 83px; top: 68px; width: 473px; height: 670px; }
  .letterhead .brand { left: 33px; top: 52px; width: 180px; }
  .letterhead .brand__name { font-size: 25px; }
  .letterhead .brand__tag { font-size: 7px; }
  .letterhead .contact { left: 318px; top: 30px; }
  .letterhead__rule { position: absolute; left: 33px; top: 91.5px; width: 407px; height: 1px; background: var(--teal); }
  .letter { position: absolute; left: 42px; top: 204px; width: 392px; }
  .letter__greeting { font-size: 10.6px; font-weight: 500; color: var(--ink); margin-left: 1px; margin-bottom: 13px; }
  .letter__body p { font-family: "Arimo", sans-serif; font-size: 8px; line-height: 9.8px; color: var(--ink-soft); margin-bottom: 8.3px; }
  .letter__closing { font-size: 6.6px; font-weight: 700; color: var(--ink); margin-top: 14px; margin-left: 1px; }
  .letterhead .footer-band { height: 40px; }

  /* Business card front */
  .card-front { left: 593px; top: 68px; width: 253px; height: 146px; }
  .card-front .brand { left: 16px; top: 58px; width: 106px; }
  .card-front .brand__name { font-size: 14px; }
  .card-front .brand__tag { font-size: 4px; }
  .card-front__divider { position: absolute; left: 126px; top: 27px; width: 1px; height: 68px; background: #777; }
  .card-front .contact { left: 133px; top: 26px; font-size: 6.3px; line-height: 7.9px; }
  .card-front .contact .gap { margin-top: 4px; }
  .card-front .icon { width: 4.8px; height: 4.8px; }
  .card-front__name { font-size: 8.4px; line-height: 10px; font-weight: 700; color: var(--name-blue); }
  .card-front .footer-band { height: 28px; }

  /* Business card back */
  .card-back { left: 863px; top: 68px; width: 255px; height: 146px; background: linear-gradient(90deg, var(--cyan), var(--blue)); }
  .card-back .brand { left: 44px; top: 66px; width: 167px; }
  .card-back .brand__name { font-size: 22px; }
  .card-back .brand__tag { font-size: 6.2px; }

  /* Envelope back with flap */
  .envelope-back { left: 593px; top: 248px; width: 525px; height: 227px; }
  .envelope-back__flap { position: absolute; left: 0; top: 0; width: 525px; height: 66px; display: block; filter: drop-shadow(0 4px 4px rgba(0,0,0,.18)); }
  .envelope-back .brand { left: 198px; top: 28px; width: 129px; }
  .envelope-back .brand__name { font-size: 17px; }
  .envelope-back .brand__tag { font-size: 5px; }

  /* Envelope front */
  .envelope-front { left: 593px; top: 510px; width: 525px; height: 228px; }
  .envelope-front .brand { left: 13px; top: 29px; width: 134px; }
  .envelope-front .brand__name { font-size: 18.5px; }
  .envelope-front .brand__tag { font-size: 5.2px; }
  .envelope-front__address { position: absolute; left: 0; top: 63px; width: 160px; text-align: center; font-style: normal; font-weight: 400; font-size: 7.8px; line-height: 9.6px; color: var(--ink); }
  .envelope-front .footer-band { height: 40px; }
</style>
</head>
<body>

<svg width="0" height="0" style="position:absolute" aria-hidden="true">
  <defs>
    <linearGradient id="flapBlue" x1="0" y1="0" x2="0" y2="1">
      <stop offset="0" stop-color="#1bb7ea"/>
      <stop offset="1" stop-color="#0a6cbb"/>
    </linearGradient>
    <symbol id="phone" viewBox="0 0 10 10"><path d="M1 3 C1 2 2 1 5 1 C8 1 9 2 9 3 L7 4 L6 3 L4 3 L3 4 Z M2 5 L8 5 L9 9 L1 9 Z"/></symbol>
    <symbol id="mail" viewBox="0 0 10 10"><path d="M1 4 L5 1 L9 4 L9 9 L1 9 Z M2 4.5 L5 7 L8 4.5 L8 4 L5 2 L2 4 Z" fill-rule="evenodd"/></symbol>
    <symbol id="globe" viewBox="0 0 10 10"><circle cx="5" cy="5" r="4.5"/></symbol>
  </defs>
</svg>

<!-- Letterhead -->
<section class="sheet letterhead">
  <div class="brand">
    <span class="brand__name">BRIGHT HAVEN</span>
    <span class="brand__tag">DENTAL IMPLANT CENTER</span>
  </div>
  <div class="contact">
    <p>4817 NW Maple Crest Rd Unit B</p>
    <p>Harbor Point, FL 00000</p>
    <p class="gap"><svg class="icon"><use href="#phone"/></svg><span>555-318-2790</span></p>
    <p><svg class="icon"><use href="#mail"/></svg><span>info@brighthavendental.example</span></p>
    <p><svg class="icon"><use href="#globe"/></svg><span>www.<span class="web">brighthavendental</span>.example</span></p>
  </div>
  <div class="letterhead__rule"></div>

  <article class="letter">
    <p class="letter__greeting">Dear Mr. Alden,</p>
    <div class="letter__body">
      <p>Lorem ipsum dolor sit amet, consectetuer adipiscing elit, sed diam nonmmy nibh euismod tincidunt ut laor eet dolore magna aliquam erat volutpat. Ut wisi enim ad minim veniam, quis nostrud exerci tationmcorper suscipit lobortis nisl ut aliquip ex ea commodo consequat. Duis autem vel eum iriure dolor in hendrerit in vulputate velit esse molestie consequat, vel illum dolore eu feugiat</p>
      <p>Rorem ipsum dolor sit amet, consectetuer adipiscing elit, sed diam nonmmy nibh euismod tincidunt ut laor eet dolore magna aliquam erat volutpat. Ut wisi enim ad minim veniam, quis nostrud exerci tationmcorper suscipit lobortis nisl ut aliquip ex ea commodo consequat. Duis autem vel eum iriure dolor in hendrerit in vulputate velit esse molest</p>
      <p>Dorem ipsum dolor sit amet, consectetuer adipiscing elit, sed diam nonmmy nibh euismod tincidunt ut laor eet dolore magna aliquam erat volutpat. Ut wisi enim ad minim veniam, quis nostrud exerci tationmcorper suscipit lobortis nisl ut aliquip ex ea commodo consequat. Duis autem vel eum iriure dolor in hendrerit in suscipit lobortis nisl ut aliquip ex ea commodo consequat. Duis autem vel eum iriure dolor in hendrerit in vulputate velit esse molestie consequat, vel illum</p>
      <p>Sorem ipsum dolor sit amet, consectetuer adipiscing elit, sed diam nonmmy nibh euismod tincidunt ut laor eet dolore magna aliquam erat volutpat. Ut wisi enim ad minim veniam, quis nostrud exerci tationmcorper suscipit lobortis nisl ut aliquip ex ea commodo consequat. Duis autem vel eum iriure dolor in</p>
    </div>
    <p class="letter__closing">Sincerely,</p>
  </article>

  <div class="footer-band" role="img" aria-label="Decorative footer band in teal and blue"></div>
</section>

<!-- Business card front -->
<section class="sheet card-front">
  <div class="brand">
    <span class="brand__name">BRIGHT HAVEN</span>
    <span class="brand__tag">DENTAL IMPLANT CENTER</span>
  </div>
  <div class="card-front__divider"></div>
  <div class="contact">
    <p class="card-front__name">Gordon Patel, DDS</p>
    <p>Bright Haven Dental Implant Center</p>
    <p class="gap">4817 NW Maple Crest Rd Unit B</p>
    <p>Harbor Point, FL 00000</p>
    <p class="gap"><svg class="icon"><use href="#phone"/></svg><span>555-318-2790</span></p>
    <p><svg class="icon"><use href="#mail"/></svg><span>info@brighthavendental.example</span></p>
    <p><svg class="icon"><use href="#globe"/></svg><span>www.<span class="web">brighthavendental</span>.example</span></p>
  </div>
  <div class="footer-band" role="img" aria-label="Decorative footer band in teal and blue"></div>
</section>

<!-- Business card back -->
<section class="sheet card-back">
  <div class="brand brand--light">
    <span class="brand__name">BRIGHT HAVEN</span>
    <span class="brand__tag">DENTAL IMPLANT CENTER</span>
  </div>
</section>

<!-- Envelope back -->
<section class="sheet envelope-back">
  <svg class="envelope-back__flap" viewBox="0 0 525 66" aria-hidden="true">
    <path d="M0 0 L525 0 L516 36 C512 52 505 62 485 62 L40 62 C20 62 13 52 10 36 Z" fill="url(#flapBlue)"/>
  </svg>
  <div class="brand brand--light">
    <span class="brand__name">BRIGHT HAVEN</span>
    <span class="brand__tag">DENTAL IMPLANT CENTER</span>
  </div>
</section>

<!-- Envelope front -->
<section class="sheet envelope-front">
  <div class="brand">
    <span class="brand__name">BRIGHT HAVEN</span>
    <span class="brand__tag">DENTAL IMPLANT CENTER</span>
  </div>
  <address class="envelope-front__address">
    4817 NW Maple Crest Rd Unit B<br>Harbor Point, FL 00000
  </address>
  <div class="footer-band" role="img" aria-label="Decorative footer band in teal and blue"></div>
</section>

</body>
</html>
```